Brochure for a website accessibility report

This brochure is related to a report that www.qelvantrix.org sell. The report shows the results of an automated audit of a websites accessibility. It shows details of issues found with screen shots, examples of code and provides remediation advice.

The brochure will be a pdf 8.5 inches by 11 inches. It can be anywhere from 6 to 10 pages.

The FlintVue™ name itself should be “Bree Serif” font. The fonts, styles, colors and sizes are up to you.

The images used and logo of the Office of Digital Reachworks and K7P logo are upload

We highlighted in blue page extracts from the report we sell. Do not use the blue highlight, it is merely there to show you where the specific examples of the report we sell are vs the other content in the report. The areas in blue which show the content from the actual report should be shown as an extract of the actual page of the report. You have flexibility to change the layout and the way the content look.

The red square callouts over the blue content are callouts that describe the specific page extracts. We used it as a red callout only so that you would be able to see it. You should change the specific location, look and feel of the callout to be appropriate

Target Market(s)

Marketing and Technical people

Industry/Entity Type

Information Technology

Font styles to use
Sans Serif

Colors

Designer to choose colors to be used in the design.

Requirements
Should not have
• wheelchairs, images of blind people

```html
<!DOCTYPE html>
<html lang="en">
<head>
<meta charset="utf-8">
<title>FlintVue™ Brochure</title>
<link href="https://fonts.googleapis.com/css2?family=Bree+Serif&family=Arimo:ital,wght@0,400;0,700;1,400&display=swap" rel="stylesheet">
<style>
:root{
  --green:#27ae6b;
  --green-dark:#1f9a5c;
  --tint:#dbeee3;
  --tint-soft:#e7f3ec;
  --ghost:#e3f1e8;
  --ink:#1d1d1d;
  --white:#ffffff;
}
*{margin:0;padding:0;box-sizing:border-box}
html,body{width:1200px;height:2954px;overflow:hidden;background:var(--white)}
body{position:relative;font-family:"Arimo",Arial,sans-serif;color:var(--ink)}
.page{position:absolute;left:0;width:1200px;height:930px}
.page-1{top:0}.page-2{top:1025px}.page-3{top:2025px}
.band-top{position:absolute;left:135px;top:0;width:1065px;height:18px;background:var(--ghost)}
.band-bottom{position:absolute;left:135px;bottom:0;width:1065px;height:18px;background:var(--ghost)}
.brand{position:absolute;left:6px;top:8px;display:flex;align-items:flex-start;gap:6px}
.brand-mark{width:14px;height:14px;background:var(--green);margin-top:2px}
.brand-name{font-family:"Arimo",sans-serif;font-weight:700;font-size:13.5px;line-height:15px;color:#111;text-transform:uppercase}
.side-name{position:absolute;left:-190px;top:420px;width:480px;transform:rotate(-90deg);font-family:"Bree Serif",serif;font-size:92px;color:var(--ghost);white-space:nowrap;text-align:center;line-height:100px}
.page-num{position:absolute;left:0;bottom:0;width:135px;height:108px;background:var(--ghost);color:var(--green);font-size:46px;display:flex;align-items:center;justify-content:center;padding-top:6px}
.product{font-family:"Bree Serif",serif}
.title{position:absolute;top:58px;left:135px;width:1040px;text-align:center;font-family:"Bree Serif",serif;font-size:33px;font-weight:400}
.body-text{font-size:17.2px;line-height:22px}
.intro{position:absolute;top:118px;left:205px;width:915px}
.intro p{margin-bottom:22px}
.facts-head{position:absolute;top:314px;left:135px;width:1040px;text-align:center;color:var(--green);font-weight:700;font-size:21px}
.facts{position:absolute;top:368px;left:180px;width:949px;display:grid;grid-template-columns:312px 310px 312px;grid-template-rows:180px 271px;column-gap:7px;row-gap:8px}
.fact{background:var(--tint);display:flex;align-items:center;justify-content:center;text-align:center;padding:0 24px;font-size:17.2px;line-height:22px}
.fact em{font-size:15.5px;line-height:20px}
.p2-intro{position:absolute;top:48px;left:165px;width:980px;text-align:justify}
.partner{position:absolute;top:168px;left:0;width:1200px;display:flex;justify-content:center;align-items:center;gap:10px}
.partner-mark{width:24px;height:24px;background:#1f5ea8}
.partner-name{font-family:"Arimo",sans-serif;font-weight:700;font-size:38px;color:#1f5ea8;letter-spacing:2px}
.wcag-head{position:absolute;top:248px;left:135px;width:1040px;text-align:center;color:var(--green);font-weight:700;font-size:21px;line-height:32px}
.principles{position:absolute;top:320px;left:178px;width:954px;display:grid;grid-template-columns:474px 474px;grid-template-rows:135px 108px;gap:6px}
.principle{background:var(--tint-soft);padding:1px 32px 0;text-align:justify;font-size:15.8px;line-height:20px}
.principle h3{color:var(--green);font-size:18px;font-weight:700;text-align:center;line-height:20px}
.principle.center p{text-align:center}
.last-line{text-align-last:center}
.p2-body{position:absolute;top:616px;left:165px;width:980px;text-align:justify}
.p2-body p{margin-bottom:22px}
.p2-body ul{list-style:none;margin-left:28px}
.p2-body li{position:relative;padding-left:20px}
.p2-body li::before{content:"";position:absolute;left:-2px;top:6px;width:10px;height:10px;background:var(--green)}
.section-head{position:absolute;top:96px;left:165px;width:980px;display:flex;align-items:center;gap:18px}
.section-head .rule{flex:1;height:3px;background:var(--green)}
.section-head h2{font-size:24px;font-weight:700}
.section-lead{position:absolute;top:138px;left:135px;width:1040px;text-align:center;font-style:italic;font-size:17.2px}
.chart-head{position:absolute;top:182px;left:165px;color:var(--green);font-weight:700;font-size:21px}
.chart-note{position:absolute;top:212px;left:273px}
.summary{position:absolute;top:280px;left:295px;width:718px;border-collapse:collapse;font-size:16.5px}
.summary th{background:var(--green);color:var(--white);font-weight:400;height:37px;border:2px solid var(--white);border-top:none}
.summary th:first-child{text-align:left;padding-left:6px;border-left:2px solid var(--green)}
.summary th:last-child{border-right:2px solid var(--green)}
.summary td{border:2px solid var(--green);height:48px}
.summary td.principle-cell{color:var(--green);font-weight:700;font-size:18px;padding-left:6px;width:158px}
.summary td.guideline{padding-left:6px;width:294px}
.summary td.issues{text-align:center}
.dot{color:var(--green);font-size:12px;margin:0 3px;vertical-align:1px}
</style>
</head>
<body>

<section class="page page-1">
  <div class="band-top"></div>
  <div class="brand"><span class="brand-mark"></span><span class="brand-name">Office of<br>Digital<br>Reachworks</span></div>
  <div class="side-name">FlintVue™</div>
  <h1 class="title">FlintVue™</h1>
  <div class="intro body-text">
    <p>The Office of Digital Reachworks (ODR) has been helping eliminate the digital accessibility divide since 2001. We have analyzed more than 51,000 websites and our reports, tools, and services help our clients ensure that their sites are accessible to everyone, regardless of any particular disability or impairment.</p>
    <p>Now, we’re offering our <b>exclusive <span class="product">FlintVue™</span> report</b>, custom-tailored to your website, to help your organization identify and rectify digital accessibility risks.</p>
    <p><span class="product">FlintVue™</span> is the most cost-effective first step on your path to compliance.</p>
  </div>
  <div class="facts-head">Quick facts:</div>
  <div class="facts">
    <div class="fact">Failure to comply with Web Content Accessibility Guidelines (WCAG) 2.1 Level A/AA could result in tens of thousands of dollars (per incident) in legal fees from pending lawsuits.</div>
    <div class="fact">Last year the number of website accessibility lawsuits increased by 177% vs. 2017.</div>
    <div class="fact">In New York state alone, 1,564 lawsuits were filed alleging websites were not accessible to the blind or visually impaired.</div>
    <div class="fact">The cost of making websites accessible ranges from several thousand dollars to a few million dollars, depending on the complexity of the site.</div>
    <div class="fact"><div>And while numerous big-name companies have been sued <em>(Varnet News, Grill Baron, Parcelon, Cocoleaf, Pixelmoor, Tunevale, Kaizora, Linen &amp; Loft, Tickerwell, Valumart, Dishrun, Green Ladle, Medrix, Slicewell, Streamly, Stridefor, Kindredly, Bank of Westmoor, Fairgrocer, Bolt Hardware, and hundreds more</em>), small businesses also face great risk.</div></div>
    <div class="fact">Trying to meet WCAG guidelines without the advantage of FlintVue™ could result in a tremendous amount of wasted time, money and effort. Don’t go it alone.</div>
  </div>
  <div class="page-num">2</div>
  <div class="band-bottom"></div>
</section>

<section class="page page-2">
  <div class="band-top"></div>
  <div class="brand"><span class="brand-mark"></span><span class="brand-name">Office of<br>Digital<br>Reachworks</span></div>
  <div class="side-name">FlintVue™</div>
  <p class="p2-intro body-text">The Americans with Disabilities Act (ADA) is a comprehensive federal civil rights law prohibiting discrimination on the basis of disability, enforced by the Department of Justice (DOJ). The ADA prohibits discriminatory lack of access for individuals with disabilities to goods and services of public services and accommodations. Websites are considered places of public accommodations. The DOJ currently uses WCAG 2.1 Level A/AA as an accepted standard by which to measure a website’s accessibility.</p>
  <div class="partner"><span class="partner-mark"></span><span class="partner-name">K7P</span></div>
  <div class="wcag-head">WCAG 2.1 Level A/AA consists of 13 guidelines with 50 checkpoints<br>that are organized under FOUR PRINCIPLES:</div>
  <div class="principles">
    <div class="principle"><h3>Principle 1: PERCEIVABLE</h3><p class="last-line">Information and user interface components must be presented to users in ways they can perceive. This means that users must be able to comprehend the information being depicted: It can’t be invisible to all their senses.</p></div>
    <div class="principle"><h3>Principle 2: OPERABLE</h3><p class="last-line">User interface components and navigation must be operable: The interface cannot require interaction that a user cannot perform.</p></div>
    <div class="principle"><h3>Principle 3: Understandable</h3><p class="last-line">Information and the operation of a user interface must be understandable: <i>Users must be able to understand the information as well as the operation of the user interface.</i></p></div>
    <div class="principle"><h3>Principle 4: ROBUST</h3><p class="last-line">Content must be robust enough that it can be interpreted reliably by a wide variety of user agents, including assistive technologies: As technologies and user agents evolve, the content should remain accessible.</p></div>
  </div>
  <div class="p2-body body-text">
    <p>Start your journey to a fully compliant website with <span class="product">FlintVue</span>™. This detailed compliance and remediation report is generated based on scanning your website against hundreds of carefully-crafted rules, logging failures, and then generating feedback and recommendations on how to fix the problems based on our years of experience and proven best practices.</p>
    <p>The <span class="product">FlintVue</span>™ report is designed to be shared with your executive team and stakeholders. It is divided into two sections to build knowledge and self-sufficiency.</p>
    <ul>
      <li>The first section provides a detailed analysis of your website per the WCAG 2.1 A/AA principles and includes an at-a-glance Summary Chart for your executive team.</li>
      <li>The second section is designed specifically for your website development team, providing them with detailed examples of problematic issues, suggested ways to fix them, and links for more detailed training.</li>
    </ul>
  </div>
  <div class="page-num">3</div>
  <div class="band-bottom"></div>
</section>

<section class="page page-3">
  <div class="band-top"></div>
  <div class="brand"><span class="brand-mark"></span><span class="brand-name">Office of<br>Digital<br>Reachworks</span></div>
  <div class="side-name">FlintVue™</div>
  <div class="section-head"><span class="rule"></span><h2>SECTION 1</h2><span class="rule"></span></div>
  <p class="section-lead">The first section of the report begins with a Summary Chart that breaks down WCAG 2.1 A/AA issues by principle:</p>
  <div class="chart-head">EXAMPLE WCAG 2.1 A/AA Summary Chart</div>
  <p class="chart-note body-text">Checkpoints with failures detected are identified in the “Issues Discovered” column.<br>The detail behind these failures is available in the next section.</p>
  <table class="summary">
    <tr><th>Principle</th><th>Guideline</th><th>Issues Discovered</th></tr>
    <tr><td class="principle-cell" rowspan="4">Perceivable</td><td class="guideline">Guideline 1.1 Text Alternatives</td><td class="issues">1.1.1</td></tr>
    <tr><td class="guideline">Guideline 1.2 Time-based Media</td><td class="issues">1.2.1<span class="dot">•</span>1.2.2<span class="dot">•</span>1.2.3<span class="dot">•</span>1.2.4<span class="dot">•</span>1.2.5</td></tr>
    <tr><td class="guideline">Guideline 1.3 Adaptable</td><td class="issues">1.3.1<span class="dot">•</span>1.3.2<span class="dot">•</span>1.3.5</td></tr>
    <tr><td class="guideline">Guideline 1.4 Distinguishable</td><td class="issues">1.4.1<span class="dot">•</span>1.4.3<span class="dot">•</span>1.4.4<span class="dot">•</span>1.4.11</td></tr>
    <tr><td class="principle-cell" rowspan="3">Operable</td><td class="guideline">Guideline 2.1 Keyboard Accessible</td><td class="issues">2.1.1<span class="dot">•</span>2.1.2</td></tr>
    <tr><td class="guideline">Guideline 2.2 Enough Time</td><td class="issues">2.2.1<span class="dot">•</span>2.2.2</td></tr>
    <tr><td class="guideline">Guideline 2.4 Navigable</td><td class="issues">2.4.1<span class="dot">•</span>2.4.2<span class="dot">•</span>2.4.4<span class="dot">•</span>2.4.7</td></tr>
    <tr><td class="principle-cell" rowspan="3">Understandable</td><td class="guideline">Guideline 3.1 Readable</td><td class="issues">3.1.1</td></tr>
    <tr><td class="guideline">Guideline 3.2 Predictable</td><td class="issues">3.2.1<span class="dot">•</span>3.2.2</td></tr>
    <tr><td class="guideline">Guideline 3.3 Input Assistance</td><td class="issues">3.3.2</td></tr>
    <tr><td class="principle-cell">Robust</td><td class="guideline">Guideline 4.1 Compatible</td><td class="issues">4.1.1<span class="dot">•</span>4.1.2</td></tr>
  </table>
  <div class="page-num">4</div>
  <div class="band-bottom"></div>
</section>

</body>
</html>
```